DESKHAVEN COSPACE Website design and coding

DESKHAVEN COSPACE

DESKHAVEN is Galveston’s first (and currently only) shared business co-working space. We share the same upscale, casual work environment, but we work independently on our own (or our team’s) projects and goals. For only a flat $195 membership fee per month, you have your very own all-inclusive, fun, personal business office environment. Website is written (Word file #12, below); and all pictures etc provided. Galveston is a beachy, coastal, historic city an hour from Houston, Texas USA. Logo (file 11 below) is temporary only.

Target Market(s)

Outside sales people, medical students looking for study hall, Houston companies looking for local office, real estate agents, graphic artists, entrepreneurs, etc

Contact Information for Business Card

will discuss --want to combine with current business card with multiple businesses

Logo Text

DESKHAVEN COSPACE

Coding

Coded - Design and coding required

Number of Pages Required

5+ page

Colors
ec1f27
fbed22

Requirements
Nice to have
• maroon/wine dominant with yellow and red accents, gray base are the colors of the space--website could coordinate--but open to creative ideas/combinations

```html
<!DOCTYPE html>
<html lang="en">
<head>
<meta charset="utf-8">
<title>DESKHAVEN COSPACE</title>
<link href="https://fonts.googleapis.com/css2?family=Montserrat:wght@600;700;800&family=Open+Sans:wght@400;600;700&display=swap" rel="stylesheet">
<style>
:root{
  --wine:#870000;
  --wine-dark:#6e0000;
  --ink:#111111;
  --text:#444444;
  --muted:#5a5a5a;
  --line:#d9d9d9;
  --white:#ffffff;
  --card-shadow:0 2px 10px rgba(0,0,0,.12);
}
*{box-sizing:border-box;margin:0;padding:0}
html,body{width:1200px;height:3452px;overflow:hidden;background:var(--white)}
body{position:relative;font-family:"Open Sans",sans-serif;color:var(--text)}
.abs{position:absolute}
.heading{font-family:"Montserrat",sans-serif;font-weight:700;color:var(--ink);text-align:center;letter-spacing:.5px}
.heading em{font-style:normal;color:var(--wine)}
.btn{position:absolute;display:flex;align-items:center;justify-content:center;background:var(--wine);color:var(--white);font-family:"Open Sans",sans-serif;font-weight:700;font-size:15px;border-radius:24px;text-transform:uppercase}

/* header */
.site-header{left:0;top:0;width:1200px;height:133px;background:var(--white)}
.brand{left:111px;top:30px;font-family:"Montserrat",sans-serif;font-weight:800;color:var(--wine);line-height:1.05;text-align:center}
.brand .l1{font-size:31px;letter-spacing:1px}
.brand .l2{font-size:22px;letter-spacing:2px}
.topbar{left:666px;top:16px;height:36px;display:flex;align-items:center;gap:10px;font-size:14px;color:var(--muted)}
.topbar .phone-dot{width:36px;height:36px;border-radius:50%;background:var(--wine);display:flex;align-items:center;justify-content:center;margin-left:4px}
.topbar .num{font-weight:700;color:var(--ink);font-size:15px;margin-left:6px}
.topbar .sep{width:1px;height:28px;background:var(--line);margin:0 18px 0 18px}
.social{display:flex;gap:11px}
.social span{width:33px;height:33px;border-radius:50%;border:2px solid var(--wine);display:block}
.nav-rule{left:461px;top:68px;width:626px;height:1px;background:var(--line)}
.nav-rule::before{content:"";position:absolute;left:0;top:-1px;width:45px;height:3px;background:var(--wine)}
.nav-caret{left:476px;top:69px;width:0;height:0;border-left:7px solid transparent;border-right:7px solid transparent;border-top:7px solid var(--wine)}
.main-nav{left:461px;top:90px;display:flex;gap:24px;font-size:15.5px;color:var(--ink)}
.main-nav .active{font-weight:700}

/* hero */
.hero{left:0;top:133px;width:1200px;height:599px;background:linear-gradient(180deg,#8f8a80 0%,#6d675d 40%,#3a3631 75%,#2a2724 100%)}
.hero-shade{left:0;top:133px;width:1200px;height:599px;background:rgba(0,0,0,.22)}
.hero-title{left:0;top:334px;width:1200px;text-align:center;font-family:"Montserrat",sans-serif;font-weight:700;font-size:37px;color:var(--white)}
.hero-copy{left:0;top:393px;width:1200px;text-align:center;font-size:18px;line-height:28px;font-weight:600;color:var(--white)}
.slide-arrow{width:36px;height:36px;border-radius:50%;border:1.5px solid var(--white);display:flex;align-items:center;justify-content:center}
.slide-arrow.dark{border-color:var(--wine)}

/* amenities */
.amenity{position:absolute;width:304px;height:158px;background:var(--white);box-shadow:var(--card-shadow);display:flex;flex-direction:column;align-items:center}
.amenity svg{margin-top:22px}
.amenity .label{position:absolute;top:108px;width:100%;text-align:center;font-size:20px;color:var(--ink)}
.amenity.featured{background:var(--wine)}
.amenity.featured .label{color:var(--white)}

/* about band */
.about-photo{left:0;top:1406px;width:600px;height:347px;background:linear-gradient(135deg,#c9b98a 0%,#6f6a5c 45%,#2f2c29 100%)}
.about-panel{left:600px;top:1406px;width:600px;height:347px;background:var(--wine)}
.about-title{left:643px;top:1440px;font-family:"Montserrat",sans-serif;font-weight:700;font-size:25px;color:var(--white)}
.about-copy{left:643px;top:1490px;width:444px;font-size:15.8px;line-height:24px;color:var(--white);text-align:justify}
.btn-outline{left:644px;top:1666px;width:133px;height:46px;background:transparent;border:2px solid var(--white)}

/* philosophy */
.post{position:absolute;top:1920px;width:311px;height:377px;background:var(--white);box-shadow:var(--card-shadow)}
.post .photo{height:218px}
.post h3{margin:16px 16px 0;font-weight:400;font-size:17.5px;color:var(--ink)}
.post p{margin:8px 16px 0;font-size:14.5px;line-height:22px;color:var(--muted)}
.post .more{position:absolute;left:15px;top:342px;display:flex;align-items:center;gap:10px;font-weight:700;font-size:15px;color:var(--wine)}
.dots{left:584px;top:2333px;display:flex;gap:6px}
.dots span{width:13px;height:13px;border-radius:50%;border:2px solid var(--wine)}
.dots span.on{background:var(--wine)}

/* gallery */
.tile{position:absolute}

/* footer */
.site-footer{left:0;top:3104px;width:1200px;height:348px;background:var(--wine)}
.foot-brand{left:111px;top:3146px;color:var(--white)}
.foot-nav{left:401px;top:3174px;display:flex;gap:21px;font-size:14.5px;font-weight:600;color:var(--white)}
.foot-social{left:966px;top:3166px}
.foot-social span{border-color:var(--white)}
.foot-rule{left:111px;width:976px;height:1px;background:rgba(255,255,255,.45)}
.contact{position:absolute;top:3276px;display:flex;gap:16px;color:var(--white)}
.contact .ico{width:34px;height:34px;border-radius:50%;border:1.5px solid var(--white);display:flex;align-items:center;justify-content:center;flex:none}
.contact h4{font-size:17.5px;font-weight:700;margin-top:-2px}
.contact p{font-size:15.5px;line-height:22px;margin-top:12px}
.copyright{left:0;top:3404px;width:1200px;text-align:center;font-size:12.5px;color:var(--white)}
</style>
</head>
<body>

<header class="abs site-header">
  <div class="abs brand"><div class="l1">DESKHAVEN</div><div class="l2">COSPACE</div></div>
  <div class="abs topbar">
    <span>Call Us Today!</span>
    <span class="phone-dot"><svg width="16" height="16" viewBox="0 0 24 24"><path fill="#fff" d="M6.6 10.8a15.1 15.1 0 0 0 6.6 6.6l2.2-2.2c.3-.3.7-.4 1-.2 1.1.4 2.3.6 3.6.6.6 0 1 .4 1 1V20c0 .6-.4 1-1 1A17 17 0 0 1 3 4c0-.6.4-1 1-1h3.5c.6 0 1 .4 1 1 0 1.3.2 2.5.6 3.6.1.3 0 .7-.2 1z"/></svg></span>
    <span class="num">713-555-0142</span>
    <span class="sep"></span>
    <div class="social"><span></span><span></span><span></span></div>
  </div>
  <div class="abs nav-rule"></div>
  <div class="abs nav-caret"></div>
  <nav class="abs main-nav">
    <span class="active">Home</span><span>About Us</span><span>Amenities</span><span>Our Services</span><span>Our Gallery</span><span>Blog</span><span>Contact Us</span>
  </nav>
</header>

<section>
  <div class="abs hero" role="img" aria-label="Photo of the coworking lounge with sofas, bar stools and desks"></div>
  <div class="abs hero-shade"></div>
  <h1 class="abs hero-title">DESKHAVEN COSPACE</h1>
  <p class="abs hero-copy">DESKHAVEN is Galveston’s first (and currently only) shared business co-working space.<br>We share the same upscale</p>
  <div class="btn" style="left:523px;top:474px;width:154px;height:46px">Get Started</div>
  <div class="abs slide-arrow" style="left:35px;top:414px"><svg width="10" height="10" viewBox="0 0 10 10"><path d="M6.5 1.5 3 5l3.5 3.5" fill="none" stroke="#fff" stroke-width="1.3"/></svg></div>
  <div class="abs slide-arrow" style="left:1127px;top:414px"><svg width="10" height="10" viewBox="0 0 10 10"><path d="M3.5 1.5 7 5 3.5 8.5" fill="none" stroke="#fff" stroke-width="1.3"/></svg></div>
</section>

<section>
  <h2 class="abs heading" style="left:0;top:810px;width:1200px;font-size:34px">AMENITIES</h2>

  <div class="amenity featured" style="left:111px;top:894px">
    <svg width="66" height="66" viewBox="0 0 66 66"><path d="M12 22a24 24 0 1 1 4 26" fill="none" stroke="#fff" stroke-width="4"/><path d="M8 20l4 6 6-4" fill="none" stroke="#fff" stroke-width="4"/><text x="35" y="40" fill="#fff" font-family="Montserrat" font-weight="800" font-size="18" text-anchor="middle">24</text></svg>
    <div class="label">24 Hour Access</div>
  </div>
  <div class="amenity" style="left:447px;top:894px">
    <svg width="66" height="66" viewBox="0 0 66 66"><path d="M13 20a28 28 0 0 1 40 0M19 26a19 19 0 0 1 28 0M25 32a10 10 0 0 1 16 0" fill="none" stroke="#870000" stroke-width="4" stroke-linecap="round"/><circle cx="33" cy="38" r="3.5" fill="#870000"/><text x="33" y="62" fill="#870000" font-family="Montserrat" font-weight="800" font-size="16" text-anchor="middle">FREE</text></svg>
    <div class="label">Free Wifi</div>
  </div>
  <div class="amenity" style="left:783px;top:894px">
    <svg width="72" height="66" viewBox="0 0 72 66"><path d="M4 26v36h64V26L36 4z" fill="none" stroke="#870000" stroke-width="3"/><rect x="16" y="12" width="40" height="30" fill="#fff" stroke="#870000" stroke-width="3"/><path d="M22 20h28M22 27h28" stroke="#870000" stroke-width="3"/><path d="M4 26l32 22 32-22M4 62l24-18M68 62 44 44" fill="none" stroke="#870000" stroke-width="3"/></svg>
    <div class="label">Mail Service</div>
  </div>
  <div class="amenity" style="left:111px;top:1084px">
    <svg width="66" height="66" viewBox="0 0 66 66"><rect x="14" y="4" width="38" height="58" rx="3" fill="none" stroke="#870000" stroke-width="3"/><rect x="20" y="12" width="16" height="20" fill="none" stroke="#870000" stroke-width="3"/><path d="M23 20a7 7 0 0 1 10 0" fill="none" stroke="#870000" stroke-width="2.5"/><rect x="20" y="38" width="36" height="9" rx="4" fill="none" stroke="#870000" stroke-width="3"/></svg>
    <div class="label">Digital Door Entry</div>
  </div>
  <div class="amenity" style="left:447px;top:1084px">
    <svg width="66" height="66" viewBox="0 0 66 66"><rect x="8" y="4" width="50" height="56" rx="4" fill="none" stroke="#870000" stroke-width="3"/><rect x="14" y="10" width="38" height="44" fill="none" stroke="#870000" stroke-width="2.5"/><circle cx="33" cy="32" r="10" fill="none" stroke="#870000" stroke-width="3"/><circle cx="33" cy="32" r="3" fill="#870000"/></svg>
    <div class="label">Private Lockable Lockers</div>
  </div>
  <div class="amenity" style="left:783px;top:1084px">
    <svg width="66" height="66" viewBox="0 0 66 66"><path d="M6 6h54M33 6v8" stroke="#870000" stroke-width="3"/><rect x="12" y="14" width="42" height="10" fill="none" stroke="#870000" stroke-width="3"/><rect x="8" y="30" width="46" height="22" fill="none" stroke="#870000" stroke-width="3"/><circle cx="36" cy="48" r="10" fill="#fff" stroke="#870000" stroke-width="3"/><circle cx="36" cy="48" r="3.5" fill="#870000"/></svg>
    <div class="label">Presentation Room</div>
  </div>

  <div class="btn" style="left:533px;top:1291px;width:134px;height:43px">View More</div>
</section>

<section>
  <div class="abs about-photo" role="img" aria-label="Photo of the open workspace with leather sofa, kitchen and glass office"></div>
  <div class="abs about-panel"></div>
  <h2 class="abs about-title">ABOUT DESKHAVEN COSPACE</h2>
  <p class="abs about-copy">DESKHAVEN is Galveston’s first (and currently only) shared business co-working space. We share the same upscale, casual work environment, but we work independently on our own (or our team’s) projects and goals. For only a flat $195 membership fee per month, you have your very own all-inclusive, fun, personal business office environment.</p>
  <div class="btn btn-outline">Read More</div>
</section>

<section>
  <h2 class="abs heading" style="left:0;top:1830px;width:1200px;font-size:34px">THE DESKHAVEN <em>PHILOSOPHY</em></h2>
  <div class="abs slide-arrow dark" style="left:35px;top:2092px;opacity:.45"><svg width="10" height="10" viewBox="0 0 10 10"><path d="M6.5 1.5 3 5l3.5 3.5" fill="none" stroke="#870000" stroke-width="1.3"/></svg></div>
  <div class="abs slide-arrow dark" style="left:1127px;top:2092px"><svg width="10" height="10" viewBox="0 0 10 10"><path d="M3.5 1.5 7 5 3.5 8.5" fill="none" stroke="#870000" stroke-width="1.3"/></svg></div>

  <article class="post" style="left:111px">
    <div class="photo" role="img" aria-label="Photo of a meeting table under pendant lamps" style="background:linear-gradient(160deg,#8d9aa6 0%,#b88f3e 55%,#3c3328 100%)"></div>
    <h3>Work Outside The Home</h3>
    <p>Free yourself for the burdens of house or school, and work in an environment that MOTIVATES</p>
    <div class="more">READ MORE <svg width="14" height="14" viewBox="0 0 14 14"><circle cx="7" cy="7" r="5.5" fill="none" stroke="#870000" stroke-width="1.6"/><path d="M5 7h4M7.3 5.2 9 7 7.3 8.8" fill="none" stroke="#870000" stroke-width="1.4"/></svg></div>
  </article>
  <article class="post" style="left:445px">
    <div class="photo" role="img" aria-label="Photo of the lounge with white sofas and lockers" style="background:linear-gradient(170deg,#9aa4ad 0%,#6b6a66 50%,#2b2a2a 100%)"></div>
    <h3>Deskhaven The Competition</h3>
    <p>Because of the flexibility, prestigious location, opportunities to meet and network with active</p>
    <div class="more">READ MORE <svg width="14" height="14" viewBox="0 0 14 14"><circle cx="7" cy="7" r="5.5" fill="none" stroke="#870000" stroke-width="1.6"/><path d="M5 7h4M7.3 5.2 9 7 7.3 8.8" fill="none" stroke="#870000" stroke-width="1.4"/></svg></div>
  </article>
  <article class="post" style="left:778px">
    <div class="photo" role="img" aria-label="Photo of a cubicle with a gaming chair" style="background:linear-gradient(165deg,#a7b0a2 0%,#5f605a 55%,#232322 100%)"></div>
    <h3>Work It Out With Your Coworkers</h3>
    <p>Free yourself for the burdens of house or school, and work in an environment that MOTIVATES</p>
    <div class="more">READ MORE <svg width="14" height="14" viewBox="0 0 14 14"><circle cx="7" cy="7" r="5.5" fill="none" stroke="#870000" stroke-width="1.6"/><path d="M5 7h4M7.3 5.2 9 7 7.3 8.8" fill="none" stroke="#870000" stroke-width="1.4"/></svg></div>
  </article>
  <div class="abs dots"><span class="on"></span><span></span></div>
</section>

<section>
  <h2 class="abs heading" style="left:0;top:2423px;width:1200px;font-size:34px">OUR <em>GALLERY</em></h2>
  <div class="tile" role="img" aria-label="Photo of the glass office and kitchen" style="left:111px;top:2502px;width:480px;height:250px;background:linear-gradient(150deg,#a9b4b8 0%,#7d7669 50%,#3a352f 100%)"></div>
  <div class="tile" role="img" aria-label="Photo of a plant on the kitchen counter" style="left:608px;top:2502px;width:226px;height:250px;background:linear-gradient(170deg,#5d5550 0%,#8c7e68 55%,#d9a99a 100%)"></div>
  <div class="tile" role="img" aria-label="Photo of a hallway with a printer" style="left:852px;top:2502px;width:235px;height:250px;background:linear-gradient(160deg,#d7c9b4 0%,#a4a29e 55%,#6a6a6a 100%)"></div>
  <div class="tile" role="img" aria-label="Photo of a cubicle chair" style="left:111px;top:2768px;width:237px;height:249px;background:linear-gradient(160deg,#d8c7a7 0%,#8b8a86 50%,#2b2b2b 100%)"></div>
  <div class="tile" role="img" aria-label="Photo of the lounge by the windows" style="left:364px;top:2768px;width:227px;height:249px;background:linear-gradient(160deg,#c8c0a6 0%,#9c9070 55%,#4a4538 100%)"></div>
  <div class="tile" role="img" aria-label="Photo of the kitchen with bar stools" style="left:608px;top:2768px;width:479px;height:249px;background:linear-gradient(160deg,#b7b5ae 0%,#7d786d 50%,#3a2a24 100%)"></div>
</section>

<footer class="abs site-footer"></footer>
<div class="abs brand foot-brand"><div class="l1" style="color:#fff">DESKHAVEN</div><div class="l2" style="color:#fff">COSPACE</div></div>
<nav class="abs foot-nav"><span>Home</span><span>About Us</span><span>Amenities</span><span>Our Services</span><span>Our Gallery</span><span>Contact Us</span></nav>
<div class="abs social foot-social"><span></span><span></span><span></span></div>
<div class="abs foot-rule" style="top:3246px"></div>

<div class="contact" style="left:111px">
  <span class="ico"><svg width="14" height="16" viewBox="0 0 14 16"><path d="M7 15s5-5.2 5-9A5 5 0 0 0 2 6c0 3.8 5 9 5 9z" fill="none" stroke="#fff" stroke-width="1.5"/><circle cx="7" cy="6" r="1.8" fill="#fff"/></svg></span>
  <div><h4>Address</h4><p>418 HARBOR AVE, STE. 204<br>GALVESTON, TX 77550</p></div>
</div>
<div class="contact" style="left:494px">
  <span class="ico"><svg width="15" height="15" viewBox="0 0 24 24"><path fill="#fff" d="M6.6 10.8a15.1 15.1 0 0 0 6.6 6.6l2.2-2.2c.3-.3.7-.4 1-.2 1.1.4 2.3.6 3.6.6.6 0 1 .4 1 1V20c0 .6-.4 1-1 1A17 17 0 0 1 3 4c0-.6.4-1 1-1h3.5c.6 0 1 .4 1 1 0 1.3.2 2.5.6 3.6.1.3 0 .7-.2 1z"/></svg></span>
  <div><h4>Phone Number</h4><p>713-555-0142</p></div>
</div>
<div class="contact" style="left:812px">
  <span class="ico"><svg width="15" height="12" viewBox="0 0 15 12"><rect x=".5" y=".5" width="14" height="11" rx="1.5" fill="#fff"/><path d="M1 1.5 7.5 7 14 1.5" fill="none" stroke="#870000" stroke-width="1.3"/></svg></span>
  <div><h4>Email Address</h4><p>hello@deskhavencospace.com</p></div>
</div>

<div class="abs foot-rule" style="top:3388px"></div>
<p class="abs copyright">Copyrights 2020 DESKHAVEN COSPACE. All rights reserved</p>

</body>
</html>
```